Maple Gable Business Card

Colors can be blue, grey and white as you see in the attached logo. Needs to have a spot for name, title, phone, email, address, and website. There also needs to be a spot for an agent's picture.

Contact Information for Business Card

See project description.

Colors

Designer to choose colors to be used in the design.

```html
<!DOCTYPE html>
<html lang="en">
<head>
<meta charset="utf-8">
<title>Maple Gable Business Card</title>
<link rel="stylesheet" href="https://fonts.googleapis.com/css2?family=Roboto:wght@400;500;700&display=swap">
<style>
  :root {
    --backdrop: #2a211d;
    --card: #2b2b2d;
    --card-edge: #1c2a3a;
    --blue: #2a7ccc;
    --white: #f2f2f2;
    --grey: #c9c9c9;
    --photo-top: #3a3a3d;
    --photo-bottom: #151518;
  }
  * { margin: 0; padding: 0; box-sizing: border-box; }
  html, body { width: 1200px; height: 716px; overflow: hidden; }
  body {
    background: var(--backdrop);
    font-family: "Roboto", Arial, sans-serif;
    position: relative;
  }
  .card {
    position: absolute;
    width: 520px;
    height: 300px;
    background: var(--card);
    overflow: hidden;
    box-shadow: 0 18px 40px rgba(0,0,0,.5);
  }
  .card-front { left: 50px; top: 208px; border-bottom: 8px solid var(--blue); }
  .card-back { left: 630px; top: 208px; }

  .brand {
    color: var(--blue);
    font-weight: 500;
    text-transform: uppercase;
    line-height: 1.15;
    display: flex;
    align-items: center;
    gap: 12px;
  }
  .brand-mark {
    width: 14px; height: 14px;
    background: var(--blue);
    flex: none;
  }
  .card-front .brand {
    position: absolute;
    left: 50%; top: 50%;
    transform: translate(-50%, -50%);
    font-size: 34px;
    letter-spacing: 1px;
  }
  .card-front .brand-sub { display: block; font-size: 17px; letter-spacing: 6px; text-align: center; }

  .card-back .brand {
    position: absolute;
    left: 40px; top: 30px;
    font-size: 22px;
    letter-spacing: 1px;
  }
  .card-back .brand-sub { display: block; font-size: 11px; letter-spacing: 4px; }

  .agent { position: absolute; left: 40px; top: 104px; color: var(--white); }
  .agent-name { color: var(--blue); font-weight: 700; font-size: 20px; }
  .agent-title { font-size: 14px; margin-top: 2px; }
  .agent-address { font-size: 13px; margin-top: 10px; line-height: 1.35; color: var(--grey); }
  .contact-list { list-style: none; margin-top: 12px; font-size: 13px; }
  .contact-list li { display: flex; align-items: center; gap: 8px; line-height: 1.6; }
  .contact-list svg { width: 12px; height: 12px; fill: var(--blue); flex: none; }
  .contact-list .accent { color: var(--blue); }

  .accent-band {
    position: absolute;
    left: 0; bottom: 0;
    width: 300px; height: 7px;
    background: var(--blue);
  }
  .agent-photo {
    position: absolute;
    right: 20px; bottom: 0;
    width: 220px; height: 200px;
    background: linear-gradient(180deg, var(--photo-top), var(--photo-bottom));
  }
</style>
</head>
<body>
  <section class="card card-front">
    <div class="brand">
      <span class="brand-mark"></span>
      <span>Maple Gable<span class="brand-sub">Real Estate</span></span>
    </div>
  </section>

  <section class="card card-back">
    <div class="brand">
      <span>Maple Gable<span class="brand-sub">Real Estate</span></span>
    </div>

    <div class="agent">
      <p class="agent-name">Daniel Reyes</p>
      <p class="agent-title">Manager</p>
      <p class="agent-address">Your address, city<br>state, ZIP 0000</p>
      <ul class="contact-list">
        <li><svg viewBox="0 0 24 24"><path d="M6.6 10.8a15 15 0 0 0 6.6 6.6l2.2-2.2a1 1 0 0 1 1-.25 11.4 11.4 0 0 0 3.6.57 1 1 0 0 1 1 1V20a1 1 0 0 1-1 1A17 17 0 0 1 3 4a1 1 0 0 1 1-1h3.5a1 1 0 0 1 1 1c0 1.25.2 2.45.57 3.57a1 1 0 0 1-.25 1z"/></svg>555-014-2270</li>
        <li><svg viewBox="0 0 24 24"><path d="M2 5h20v14H2z M2 5l10 8 10-8" fill="none" stroke="#2a7ccc" stroke-width="2"/></svg>hello@maplegable.co</li>
        <li><svg viewBox="0 0 24 24"><circle cx="12" cy="12" r="9" fill="none" stroke="#2a7ccc" stroke-width="2"/><path d="M3 12h18M12 3c3 3 3 15 0 18M12 3c-3 3-3 15 0 18" fill="none" stroke="#2a7ccc" stroke-width="1.5"/></svg>www.<span class="accent">maplegablehomes</span>.com</li>
      </ul>
    </div>

    <div class="accent-band"></div>
    <div class="agent-photo" role="img" aria-label="Portrait photo of the agent in a dark suit and blue tie"></div>
  </section>
</body>
</html>
```